Anzeigengestaltung für eine Hausarztpraxis
Zielgruppe
Wir sind eine Hausarztpraxis mit zwei Standorten und suchen eine Ärztin oder einen Arzt zur Anstellung in der klassischen Hausarzt Medizin am Standort Lindenau
Aufgabenstellung
Bitte beachtet den Text im Anhang, der ist schon vorgegeben. (Anzeigentext)
Wir suchen ein ruhiges, hochwertiges Layout für eine Stellenanzeige einer Hausarztpraxis in einem historischen Gebäude.
Der Text steht im Vordergrund, das Design soll zurückhaltend, klar und wertig sein.
Bitte keine Icons, keine bunten Farben, keine verspielten Elemente.
Gerne viel Weissraum, klare Typografie, ruhige Anmutung.
Schrift: Garamond für den Fliesstext (bereits gewählt).
Das Layout soll sowohl als PDF wie auch online funktionieren.
Optional: ein sehr dezentes grafisches Element oder eine ruhige Bildanmutung (z. B. Struktur, Licht, Architekturdetail).

```html
<!DOCTYPE html>
<html lang="de">
<head>
<meta charset="utf-8">
<title>Stellenanzeige Hausarztpraxis Lindenau</title>
<link href="https://fonts.googleapis.com/css2?family=Fira+Sans:wght@400;500&family=Open+Sans:ital,wght@0,400;0,600;1,400&display=swap" rel="stylesheet">
<style>
  :root {
    --bg: #ecebe8;
    --paper: #f7f7f6;
    --ink: #2a2a2a;
    --ink-soft: #3b3b3b;
    --green: #7cc21a;
    --facade-a: #e9e6e2;
  }
  * { box-sizing: border-box; margin: 0; padding: 0; }
  html, body { width: 1200px; height: 2396px; overflow: hidden; }
  body { background: var(--bg); font-family: "Open Sans", sans-serif; color: var(--ink); }

  .ad {
    position: absolute; left: 20px; top: 377px;
    width: 1160px; height: 1641px;
    background: var(--paper);
    border-top: 3px solid var(--green);
    border-bottom: 3px solid var(--green);
    overflow: hidden;
  }
  .facade { position: absolute; left: 0; width: 100%; }
  .facade--top { top: 0; height: 130px; background: linear-gradient(180deg, var(--facade-a), var(--paper)); }
  .facade--bottom { bottom: 0; height: 200px; background: linear-gradient(0deg, var(--facade-a), var(--paper)); }

  .headline {
    position: absolute; left: 130px; top: 130px;
    border-left: 6px solid var(--green);
    padding-left: 31px;
    font-family: "Fira Sans", sans-serif; font-weight: 500;
    font-size: 33px; line-height: 39px; color: var(--ink);
    width: 330px;
  }
  .column { position: absolute; font-size: 19.5px; line-height: 35px; color: var(--ink-soft); hyphens: auto; }
  .column--left { left: 130px; top: 374px; width: 400px; }
  .column--right { left: 647px; top: 145px; width: 400px; }
  .lead { font-style: italic; }
  .gap-1 { margin-top: 47px; }
  .gap-2 { margin-top: 62px; }
  .gap-3 { margin-top: 116px; }

  .section-title {
    font-family: "Fira Sans", sans-serif; font-weight: 400;
    font-size: 26px; line-height: 32px; color: var(--ink);
    width: 330px; padding-bottom: 10px;
    border-bottom: 2px solid var(--green);
    margin-bottom: 22px;
  }
  .section + .section { margin-top: 58px; }

  .closing {
    position: absolute; left: 130px; top: 1303px; width: 920px;
    font-style: italic; font-size: 19px; line-height: 35px; color: var(--ink-soft);
  }
  .brand {
    position: absolute; left: 130px; top: 1500px;
    display: flex; align-items: center; gap: 10px;
    font-size: 15px; font-weight: 400; color: var(--ink-soft);
  }
  .brand__dot { width: 14px; height: 14px; border-radius: 50%; background: var(--green); }
  .contact {
    position: absolute; left: 647px; top: 1482px;
    font-style: normal;
    font-size: 18.5px; line-height: 25px; color: var(--ink);
  }
  .contact__mail { font-weight: 600; }
</style>
</head>
<body>
  <article class="ad">
    <div class="facade facade--top" role="img" aria-label="Dezente Fassadenansicht mit historischen Fenstern und Fensterläden"></div>
    <div class="facade facade--bottom" role="img" aria-label="Dezente Fassadenansicht mit historischen Fenstern und Fensterläden"></div>

    <h1 class="headline">Hausarztmedizin mit Tiefe – dort, wo man noch echte Grundversorgung lebt</h1>

    <div class="column column--left">
      <p class="lead">Ein Ort, der trägt. Ein Team, das bleibt. Eine Arbeit, die Wertschätzung hat.</p>
      <p class="gap-1">Manche Orte verändern die Art, wie man arbeitet. Unsere Praxis in Lindenau ist so ein Ort.</p>
      <p class="gap-2">In einem historischen Gebäude gelegen, mit grosszügigem Ambiente, warmen Vertäfelungen und kunstvoller Wandbemalung, entstehen hier Behandlungsräume von Ruhe und Würde. Kein steriler Praxisalltag, sondern ein Ort, der Gespräche trägt und medizinische Arbeit unterstützt.</p>
      <p class="gap-3">Für diesen besonderen Ort suchen wir eine Hausärztin oder einen Hausarzt, die oder der nicht einfach einen Arbeitsplatz sucht, sondern einen Platz, an dem Medizin menschlich sein darf.</p>
    </div>

    <div class="column column--right">
      <section class="section">
        <h2 class="section-title">Ein Team mit Haltung</h2>
        <p>Sie arbeiten in einem freundlichen, über Jahre gewachsenen Team mit hoher personeller Kontinuität und geringer Fluktuation.</p>
      </section>
      <section class="section">
        <h2 class="section-title">Zeit für gute Medizin</h2>
        <p>Unsere Patientinnen und Patienten sind überwiegend gut bis sehr gut situiert, wertschätzend und therapieoffen. Das ermöglicht ruhiges, strukturiertes Arbeiten mit Fokus auf Qualität, Beziehung und nachhaltige Behandlung.</p>
      </section>
      <section class="section">
        <h2 class="section-title">Und sonst?</h2>
        <p>Der Praxisalltag ist klar strukturiert, ruhig und verlässlich. Geregelte und in Abstimmung flexible Arbeitszeiten ohne Wochenend- oder Nachtdienste, eine sehr gute leistungsbezogene Vergütung sowie ein respektvoller, wertschätzender Umgang auf Augenhöhe schaffen ein Umfeld, in dem man sich auf die medizinische Arbeit konzentrieren und langfristig wohlfühlen kann.</p>
      </section>
    </div>

    <p class="closing">Wir freuen uns über eine unkomplizierte Kontaktaufnahme per E-Mail oder Telefon – gerne auch ganz unverbindlich und ohne vollständige Bewerbungsunterlagen.</p>

    <div class="brand"><span class="brand__dot"></span>Arztpraxis Lindenhof</div>

    <address class="contact">
      <div class="contact__mail">Helga.Weißmoor@arztpraxis-lindenhof.ch</div>
      <div>Arztpraxis Lindenhof, Mattenweg 7,</div>
      <div>4712 Lindenau, Tel: 0621234567</div>
    </address>
  </article>
</body>
</html>
```